Online shopping portal - Business Card Design

Brivamart.com.au is a complete shopping experience. Search, compare & buy items from partnered stores & receive cashbash for your purchases and referrals.
Mission
Our mission is to provide a system for entrepreneurs to create an ongoing income, while providing consumers worldwide with a better way to shop.
A product brokerage and Internet marketing company that specialises in One-to-One Marketing, Quellon Oceania is a subsidiary of Dorvex Holdings Global, Inc.
With more than 3 million Preferred Customers and 180,000 Customer Managers worldwide, Dorvex Holdings has generated over $3 billion USD in accumulated retail sales. The Company employs more than 675 people globally with international operations in Australia, United States, Canada, Taiwan, Hong Kong, Mexico & Singapore
Through revolutionary technology and the one-to-one marketing and social shopping Quellon Oceania are leveraging the Internet with the power of people to create the economy of the future.
By providing online shoppers with the products and services they want and need — backed by the Company’s people power — Quellon Oceania is fast becoming the World Wide Web’s ultimate online shopping destination.
As a result, we are changing the way people shop and changing the economic paradigm where anyone can become financially independent by creating their own economy — Made with Goods. Driven by Folks®.
Description
Welcome to a new kind of comparison shopping site where you get PAID cashback to shop!
Simply create an account to start accumulating cash backs each time you make purchases across hundreds of trusted Partner Stores and thousands of your favorite brands through our convenient PixBasket® for one stop shopping.
All merchant stores are backed by GLIMVEN.NET's 100% satisfaction guarantee.

Updates
Project Deadline Extended
Reason: Hi all,  I am extending the deadline as i'm going to be away for my birthday (and may not have time to check before the current deadline anyway)  I figure that the more time i give you the better.

Industry/Entity Type
Online Shopping
Contact Information for Business Card
Business Name: Brivamart.com.au
website: www.brivamart.com.au
Facebook: www.facebook.com/brivamart.com.au.
Email: info@brivamart.com.au
Phone: Lorn on 0487 52 19 64
Requirements
Nice to have
- Create a Brivamart logo

```html
<!DOCTYPE html>
<html lang="en">
<head>
<meta charset="utf-8">
<title>Brivamart.com.au – Business Card</title>
<link rel="stylesheet" href="https://fonts.googleapis.com/css2?family=Jura:wght@500;600;700&display=swap">
<style>
  :root {
    --page-bg: #e6e8eb;
    --card-white: #ffffff;
    --card-grey: #dcdfe2;
    --blue-glow: #00eef6;
    --blue-mid: #17b4da;
    --blue-deep: #1b6aa9;
    --stripe-navy: #22509b;
    --logo-blue: #1c5fa8;
    --text-light: #ffffff;
  }
  * { box-sizing: border-box; margin: 0; padding: 0; }
  html, body {
    width: 1200px; height: 900px; overflow: hidden;
    background: var(--page-bg);
    font-family: "Jura", sans-serif;
  }
  .canvas {
    width: 1200px; height: 900px;
    display: flex; flex-direction: column; align-items: center; justify-content: center;
    gap: 36px;
  }
  .card {
    position: relative;
    width: 700px; height: 400px;
    background: var(--card-white);
    box-shadow: 0 10px 30px rgba(0,0,0,0.18);
    overflow: hidden;
  }
  .card-front .art { position: absolute; inset: 0; }
  .contact {
    position: absolute; left: 44px; top: 36px;
    color: var(--text-light);
  }
  .contact .name { font-size: 25px; font-weight: 600; letter-spacing: 1.5px; }
  .contact .title { font-size: 17px; font-weight: 500; margin-top: 2px; }
  .contact .address { font-size: 20px; font-weight: 600; line-height: 1.3; margin-top: 28px; }
  .contact .lines { list-style: none; margin-top: 24px; }
  .contact .lines li {
    display: flex; align-items: center; gap: 12px;
    font-size: 18px; font-weight: 600; letter-spacing: 1px;
    height: 30px;
  }
  .contact .lines svg { width: 20px; height: 20px; flex: none; }
  .brand {
    position: absolute;
    font-family: "Jura", sans-serif;
    font-weight: 700;
    color: var(--logo-blue);
    white-space: nowrap;
  }
  .card-front .brand {
    left: 456px; right: 14px; top: 182px;
    font-size: 25px; text-align: center;
  }
  .card-back {
    background: radial-gradient(ellipse at 50% 45%, var(--card-white) 35%, var(--card-grey) 100%);
  }
  .card-back .brand {
    left: 50%; top: 50%; transform: translate(-50%, -50%);
    font-size: 52px;
  }
</style>
</head>
<body>
<main class="canvas">

  <section class="card card-front" aria-label="Business card, front">
    <svg class="art" viewBox="0 0 700 400" width="700" height="400" aria-hidden="true">
      <defs>
        <radialGradient id="blueField" cx="230" cy="230" r="330" gradientUnits="userSpaceOnUse">
          <stop offset="0" stop-color="var(--blue-glow)"/>
          <stop offset="0.45" stop-color="var(--blue-mid)"/>
          <stop offset="1" stop-color="var(--blue-deep)"/>
        </radialGradient>
      </defs>
      <path d="M0 0 H436 Q372 250 492 400 H0 Z" fill="url(#blueField)"/>
      <path d="M448 0 H462 Q392 250 508 400 H504 Q384 250 448 0 Z" fill="var(--stripe-navy)"/>
    </svg>

    <div class="contact">
      <p class="name">LORN HAVICK</p>
      <p class="title">Managing Director</p>
      <p class="address">417.12th floor,Kestrel<br>Arcade Road VND</p>
      <ul class="lines">
        <li>
          <svg viewBox="0 0 20 20"><path d="M5 2 L8 2 L9 6 L7 8 Q9 12 12 13 L14 11 L18 12 L18 15 Q17 18 14 18 Q4 16 2 5 Q2 2 5 2 Z" fill="#fff"/></svg>
          0487 52 19 64
        </li>
        <li>
          <svg viewBox="0 0 20 20"><rect x="5" y="1" width="10" height="18" rx="2" fill="none" stroke="#fff" stroke-width="1.8"/><circle cx="10" cy="16" r="1" fill="#fff"/></svg>
          0487 52 19 64
        </li>
        <li>
          <svg viewBox="0 0 20 20"><rect x="6" y="2" width="8" height="6" fill="#fff"/><rect x="2" y="8" width="16" height="10" rx="1" fill="#fff"/><rect x="5" y="11" width="10" height="1.5" fill="var(--blue-deep)"/><rect x="5" y="14" width="10" height="1.5" fill="var(--blue-deep)"/></svg>
          0487 52 19 64
        </li>
        <li>
          <svg viewBox="0 0 20 20"><rect x="1" y="4" width="18" height="12" fill="none" stroke="#fff" stroke-width="1.8"/><path d="M1 4 L10 11 L19 4" fill="none" stroke="#fff" stroke-width="1.8"/></svg>
          info@brivamart.com.au
        </li>
        <li>
          <svg viewBox="0 0 20 20"><circle cx="10" cy="10" r="8" fill="none" stroke="#fff" stroke-width="1.6"/><ellipse cx="10" cy="10" rx="3.5" ry="8" fill="none" stroke="#fff" stroke-width="1.4"/><path d="M2 10 H18 M3.5 6 H16.5 M3.5 14 H16.5" stroke="#fff" stroke-width="1.2"/></svg>
          www.brivamart.com.au
        </li>
      </ul>
    </div>

    <p class="brand">Brivamart.com.au</p>
  </section>

  <section class="card card-back" aria-label="Business card, back">
    <p class="brand">Brivamart.com.au</p>
  </section>

</main>
</body>
</html>
```